Mosquito and outdoor pest management

The uploaded logo must be integrated as the main theme of the card. I would like it to be modern and eye catching. Maybe some backround images or light silver metallic background.
Space enough at the base for contact info to be put in- phone numbers,emails,names,website.
Space on the back for short blog and lines for hand writing..calling card.
Commercial- golf courses, schools, outdoor function properties, pre event treatments.
Residential- retirement villages, townhome complexes and general houses
Management

```html
<!DOCTYPE html>
<html lang="en">
<head>
<meta charset="utf-8">
<title>Bayline Mosquito – Business Card</title>
<link rel="stylesheet" href="https://fonts.googleapis.com/css2?family=Lato:wght@400;700;900&display=swap">
<style>
  :root {
    --stage: #2b2b2b;
    --card: #fafafa;
    --card-shade: #ececec;
    --red: #d91f2a;
    --red-dark: #b3141e;
    --ink: #1d1d1d;
    --rule: #d6d6d6;
    --white: #ffffff;
  }
  * { box-sizing: border-box; margin: 0; padding: 0; }
  html, body {
    width: 1200px; height: 997px; overflow: hidden;
    background: var(--stage);
    font-family: "Lato", Arial, sans-serif;
  }
  .canvas {
    position: relative; width: 1200px; height: 997px;
    display: flex; flex-direction: column; align-items: center; justify-content: center; gap: 56px;
  }
  .card {
    position: relative; width: 720px; height: 410px;
    border-radius: 22px; overflow: hidden;
    background: linear-gradient(160deg, var(--white) 0%, var(--card) 55%, var(--card-shade) 100%);
  }
  /* Red band shared by both sides */
  .band {
    position: absolute; left: 0; right: 0; height: 70px;
    background: linear-gradient(180deg, var(--red) 0%, var(--red-dark) 100%);
    display: flex; align-items: center;
  }
  .band::before, .band::after {
    content: ""; position: absolute; left: 0; right: 0; height: 3px; background: var(--red);
  }
  .band::before { top: -10px; }
  .band::after { bottom: -10px; }
  .band__text {
    color: var(--white); font-size: 24px; letter-spacing: 2px; font-weight: 400;
  }

  /* Back side */
  .card--back .writing-lines {
    position: absolute; left: 90px; right: 40px; top: 48px;
    display: flex; flex-direction: column; gap: 48px;
  }
  .card--back .writing-lines span { display: block; height: 1px; background: var(--rule); }
  .card--back .brand { position: absolute; left: 200px; top: 236px; }
  .card--back .band { bottom: 36px; padding-left: 220px; }

  /* Front side */
  .brand {
    color: var(--ink); font-weight: 900; font-size: 34px; letter-spacing: 0.5px;
    display: flex; align-items: center; gap: 12px;
  }
  .brand__dot { width: 16px; height: 16px; border-radius: 50%; background: var(--red); }
  .card--front .brand { position: absolute; left: 56px; top: 118px; }
  .divider {
    position: absolute; left: 392px; top: 44px; width: 3px; height: 150px;
    background: linear-gradient(180deg, rgba(217,31,42,0) 0%, var(--red) 45%, rgba(217,31,42,0) 100%);
  }
  .contact { position: absolute; left: 428px; top: 36px; width: 280px; }
  .contact__name { color: var(--red); font-weight: 700; font-size: 26px; }
  .contact__role { color: var(--ink); font-weight: 700; font-size: 15px; margin-top: 2px; }
  .contact__list { list-style: none; margin-top: 22px; display: flex; flex-direction: column; gap: 8px; }
  .contact__item { display: flex; align-items: flex-start; gap: 10px; font-size: 14px; color: var(--ink); line-height: 1.5; }
  .contact__icon {
    flex: none; width: 22px; height: 22px; border-radius: 5px; background: var(--red);
    display: flex; align-items: center; justify-content: center;
  }
  .card--front .band { bottom: 60px; justify-content: center; }
</style>
</head>
<body>
<main class="canvas">
  <section class="card card--back" aria-label="Card back">
    <div class="writing-lines"><span></span><span></span><span></span><span></span></div>
    <div class="brand">Bayline Mosquito</div>
    <div class="band"><span class="band__text">The Pest Managers</span></div>
  </section>

  <section class="card card--front" aria-label="Card front">
    <div class="brand"><span class="brand__dot"></span>Bayline Mosquito</div>
    <div class="divider"></div>
    <div class="contact">
      <h1 class="contact__name">Ryan Holloway</h1>
      <p class="contact__role">Creative Director</p>
      <ul class="contact__list">
        <li class="contact__item">
          <span class="contact__icon"><svg width="14" height="14" viewBox="0 0 24 24"><path fill="#fff" d="M6.6 10.8a15 15 0 0 0 6.6 6.6l2.2-2.2c.3-.3.7-.4 1-.2 1.1.4 2.3.6 3.6.6.6 0 1 .4 1 1V20c0 .6-.4 1-1 1C10.6 21 3 13.4 3 4c0-.6.4-1 1-1h3.5c.6 0 1 .4 1 1 0 1.3.2 2.5.6 3.6.1.3 0 .7-.2 1z"/></svg></span>
          +44 100-200-300
        </li>
        <li class="contact__item">
          <span class="contact__icon"><svg width="14" height="14" viewBox="0 0 24 24"><path fill="#fff" d="M3 5h18v14H3z"/><path fill="none" stroke="#d91f2a" stroke-width="2" d="M3 6l9 7 9-7"/></svg></span>
          ryan@baylinepest.com
        </li>
        <li class="contact__item">
          <span class="contact__icon"><svg width="14" height="14" viewBox="0 0 24 24"><path fill="#fff" d="M12 2a7 7 0 0 0-7 7c0 5 7 13 7 13s7-8 7-13a7 7 0 0 0-7-7zm0 9.5A2.5 2.5 0 1 1 12 6.5a2.5 2.5 0 0 1 0 5z"/></svg></span>
          <span>#7, Harbour Lane, Westfield<br>Street, Leeds, LS9 2AB</span>
        </li>
      </ul>
    </div>
    <div class="band"><span class="band__text">www.baylinepest.com</span></div>
  </section>
</main>
</body>
</html>
```